TK Homes - Stone Dorf Design

Looking for a double sides design, 1 side for my realestate and the other for home building. ( TK Homes on 1 side, Stone Dorf card on the other Side
Side 1 - Marek Tove ~ Vox Realty logo and Company ( the Property quarter )
Marek Tove
Marek@Marektove.example
IG - Marek_Bzq_Realtor
FB - marekt
Cell - 5558130467
3847 61 St Nw

Side 2
Marek Tove
5558130467
IG - Stonedorf_Bzq
Stonedorfdev@mailbox.example

Target Market(s)

Home buyers/ sellers

Industry/Entity Type

Home builders - Realestate

Contact Information for Business Card

Above

Requirements
Must have
• Black OR White background - my information -

```html
<!DOCTYPE html>
<html lang="en">
<head>
<meta charset="utf-8">
<title>TK Homes / Stone Dorf Design – Business Cards</title>
<link href="https://fonts.googleapis.com/css2?family=Tinos:wght@400;700&display=swap" rel="stylesheet">
<style>
  :root {
    --page: #e9e9eb;
    --card: #1d1e22;
    --card-shade: #16171a;
    --card-panel: #232428;
    --blue: #1673c8;
    --gold: #f2c12e;
    --white: #f4f4f4;
  }
  * { box-sizing: border-box; margin: 0; padding: 0; }
  html, body { width: 1200px; height: 780px; overflow: hidden; }
  body {
    background: var(--page);
    font-family: "Tinos", "Times New Roman", serif;
    display: flex;
    align-items: center;
    justify-content: center;
    gap: 40px;
  }
  .card {
    position: relative;
    width: 540px;
    height: 309px;
    background: var(--card);
    overflow: hidden;
    box-shadow: 0 8px 24px rgba(0,0,0,.25);
  }
  .card__backdrop { position: absolute; inset: 0; width: 100%; height: 100%; }
  .card__content {
    position: absolute;
    right: 46px;
    top: 40px;
    text-align: right;
    color: var(--white);
  }
  .brand {
    display: flex;
    align-items: center;
    justify-content: flex-end;
    gap: 8px;
    color: var(--blue);
    font-weight: 400;
    font-size: 26px;
    letter-spacing: 2px;
    text-transform: uppercase;
    margin-bottom: 14px;
  }
  .brand__mark { width: 12px; height: 12px; background: var(--blue); }
  .person-name { font-weight: 700; font-size: 30px; line-height: 1; }
  .person-name__first { color: var(--blue); }
  .person-name__last { color: var(--gold); }
  .person-role { font-weight: 700; font-size: 15px; margin: 4px 0 14px; }
  .contact-list { list-style: none; font-size: 13px; line-height: 19px; }
  .contact-list li { display: flex; align-items: center; justify-content: flex-end; gap: 7px; }
  .contact-icon { width: 12px; height: 12px; flex: none; }
  .edge-bars { position: absolute; right: 0; width: 30px; }
  .edge-bars span { display: block; height: 11px; background: var(--blue); margin-bottom: 3px; margin-left: auto; }
</style>
</head>
<body>

<section class="card card--realty" aria-label="TK Homes realty side">
  <svg class="card__backdrop" viewBox="0 0 540 309" aria-hidden="true">
    <polygon points="0,0 210,0 120,309 0,309" fill="var(--card-shade)"/>
    <polygon points="60,0 150,0 90,309 20,309" fill="var(--card-panel)"/>
  </svg>
  <div class="edge-bars" style="top:150px">
    <span style="width:30px"></span><span style="width:24px"></span><span style="width:30px"></span>
  </div>
  <div class="card__content">
    <div class="brand"><span class="brand__mark"></span>Marek Tove</div>
    <div class="person-name"><span class="person-name__first">Marek</span> <span class="person-name__last">Tove</span></div>
    <div class="person-role">Director</div>
    <ul class="contact-list">
      <li>5558130467 <svg class="contact-icon" viewBox="0 0 12 12"><path d="M3 1l2 2-1 1.5c.8 1.6 1.9 2.7 3.5 3.5L9 7l2 2-1.5 2C5 10.5 1.5 7 1 2.5z" fill="var(--blue)"/></svg></li>
      <li>marekt <svg class="contact-icon" viewBox="0 0 12 12"><circle cx="6" cy="6" r="5.5" fill="var(--blue)"/></svg></li>
      <li>Marek_Bzq_Realtor <svg class="contact-icon" viewBox="0 0 12 12"><rect x="1" y="1" width="10" height="10" rx="2" fill="var(--blue)"/></svg></li>
      <li>Marek@Marektove.example <svg class="contact-icon" viewBox="0 0 12 12"><rect x="1" y="2.5" width="10" height="7" fill="var(--blue)"/><path d="M1 2.5l5 4 5-4" stroke="var(--card)" fill="none"/></svg></li>
      <li>www.marektove.example <svg class="contact-icon" viewBox="0 0 12 12"><circle cx="6" cy="6" r="5" fill="none" stroke="var(--blue)" stroke-width="1.3"/><ellipse cx="6" cy="6" rx="2" ry="5" fill="none" stroke="var(--blue)"/><path d="M1 6h10" stroke="var(--blue)"/></svg></li>
      <li>3847 61 St Nw <svg class="contact-icon" viewBox="0 0 12 12"><path d="M6 11.5S2 7 2 4.5a4 4 0 018 0C10 7 6 11.5 6 11.5z" fill="var(--blue)"/><circle cx="6" cy="4.5" r="1.5" fill="var(--card)"/></svg></li>
    </ul>
  </div>
</section>

<section class="card card--builder" aria-label="Stone Dorf Developments side">
  <svg class="card__backdrop" viewBox="0 0 540 309" aria-hidden="true">
    <polygon points="0,0 230,0 60,309 0,309" fill="var(--card-shade)"/>
    <polygon points="110,0 250,0 110,309 70,309" fill="var(--card-panel)"/>
  </svg>
  <div class="edge-bars" style="top:170px">
    <span style="width:30px"></span><span style="width:24px"></span><span style="width:30px"></span>
  </div>
  <div class="card__content" style="top:62px">
    <div class="brand"><span class="brand__mark"></span>Stone Dorf Developments</div>
    <div class="person-name"><span class="person-name__first">Marek</span> <span class="person-name__last">Tove</span></div>
    <div class="person-role">Director</div>
    <ul class="contact-list">
      <li>5558130467 <svg class="contact-icon" viewBox="0 0 12 12"><path d="M3 1l2 2-1 1.5c.8 1.6 1.9 2.7 3.5 3.5L9 7l2 2-1.5 2C5 10.5 1.5 7 1 2.5z" fill="var(--blue)"/></svg></li>
      <li>Stonedorf_Bzq <svg class="contact-icon" viewBox="0 0 12 12"><rect x="1" y="1" width="10" height="10" rx="2" fill="var(--blue)"/></svg></li>
      <li>Stonedorfdev@mailbox.example <svg class="contact-icon" viewBox="0 0 12 12"><rect x="1" y="2.5" width="10" height="7" fill="var(--blue)"/><path d="M1 2.5l5 4 5-4" stroke="var(--card)" fill="none"/></svg></li>
    </ul>
  </div>
</section>

</body>
</html>
```